Business Card Design for my Real Estate Investing Company

This is for a Real Estate Investing Company that will be serving the Las Vegas Valley. Id like the following slogan included: "Building Value Together" I have attached my logo. You will see the color tones I'm interested in..in my logo. I would like the card to be double-sided with a modern, professional look.
Target Market(s)
Homeowners, banks, real estate industry
Industry/Entity Type
Real Estate
Contact Information for Business Card
name: Dale Harwick
position: Managing Member
address: 4821 Corliss Pkwy ste 207-300
Cedar Hollow, NV 89321
phone: (702) 555-0143
fax: (702) 555-0187
email: SummitRidgeEstate@hollowmail.test
web: SummitRidgeEstates.test
*At the bottom of the card I would like....
We buy houses for cash....no repairs, no commissions, no fees!
Logo Text
SUMMIT RIDGE ESTATES "Investing in Our Community"
Font styles to use
Other font styles liked:
- Lora
Requirements
Must have
- On the back of the card, i'd like to have my logo large and the following statements:
- Are you considering selling your home? Want a simple, hassle-free transaction? We can help! We buy houses for cash and can close quickly! No need to do any repairs, no realtor commissions, no closing costs.....and no headaches. Let us help you with your real estate needs...!
Nice to have
- multiple colors 2 two tone on front and back

```html
<!DOCTYPE html>
<html lang="en">
<head>
<meta charset="utf-8">
<title>Summit Ridge Estates – Business Card</title>
<link href="https://fonts.googleapis.com/css2?family=Arimo:wght@400;700&family=Lora:ital,wght@0,400;0,700;1,400&display=swap" rel="stylesheet">
<style>
  :root{
    --stage:#2b2b2d;
    --brand-blue:#1f63b8;
    --brand-blue-deep:#1552a0;
    --brand-blue-light:#2f78cc;
    --ink:#1c1c1c;
    --ink-soft:#3a3a3a;
    --paper:#ffffff;
    --paper-shade:#e9e9ea;
    --navy:#10284a;
  }
  *{box-sizing:border-box;margin:0;padding:0}
  html,body{width:1200px;height:997px;overflow:hidden}
  body{background:var(--stage);position:relative;font-family:"Arimo",Arial,sans-serif}

  .card{position:absolute;width:620px;height:360px;border-radius:22px;overflow:hidden;box-shadow:0 18px 40px rgba(0,0,0,.55)}

  /* Back side */
  .card--back{left:80px;top:80px;background:linear-gradient(160deg,var(--brand-blue-light),var(--brand-blue) 55%,var(--brand-blue-deep));color:var(--paper);text-align:center}
  .card--back .brand{margin-top:58px}
  .card--back .brand-name{font-family:"Lora",Georgia,serif;font-weight:700;font-size:38px;letter-spacing:1px;color:var(--paper);display:inline-flex;align-items:center;gap:12px}
  .card--back .brand-mark{width:26px;height:26px;background:var(--paper)}
  .card--back .brand-slogan{font-family:"Lora",Georgia,serif;font-style:italic;font-size:15px;letter-spacing:2px;margin-top:6px}
  .pitch{margin-top:34px;font-size:14px;line-height:1.7}
  .pitch .pitch-close{color:var(--navy);font-weight:700}

  /* Front side */
  .card--front{left:500px;top:500px;background:linear-gradient(135deg,var(--paper) 40%,var(--paper-shade))}
  .card--front .brand{position:absolute;left:44px;top:42px}
  .card--front .brand-name{font-family:"Lora",Georgia,serif;font-weight:700;font-size:28px;color:var(--brand-blue);display:flex;align-items:center;gap:10px;letter-spacing:.5px}
  .card--front .brand-mark{width:20px;height:20px;background:var(--brand-blue)}
  .card--front .brand-slogan{font-family:"Lora",Georgia,serif;font-style:italic;font-size:12px;letter-spacing:2px;color:var(--ink-soft);margin:4px 0 0 30px}

  .holder{position:absolute;right:44px;top:116px;text-align:right;border-bottom:2px solid var(--brand-blue);padding-bottom:3px;width:210px}
  .holder-name{font-size:22px;font-weight:700;color:var(--brand-blue)}
  .holder-role{font-size:13px;color:var(--ink)}

  .divider{position:absolute;left:40px;right:40px;top:196px;height:2px;background:var(--brand-blue)}

  .contacts{position:absolute;left:44px;top:214px;list-style:none}
  .contacts li{display:flex;align-items:center;gap:10px;font-size:14px;color:var(--ink);height:22px}
  .contacts li.web{color:var(--brand-blue);font-weight:700}
  .contacts svg{width:15px;height:15px;flex:none}

  .office{position:absolute;right:44px;top:216px;text-align:right;font-size:13px;color:var(--ink);line-height:1.35}
  .office-name{font-size:15px;font-weight:700;color:var(--brand-blue)}

  .tagline-band{position:absolute;left:0;right:0;bottom:0;height:44px;background:var(--brand-blue);color:var(--paper);font-size:15px;display:flex;align-items:center;justify-content:center;letter-spacing:.3px}
</style>
</head>
<body>

<section class="card card--back" aria-label="Card back">
  <div class="brand">
    <div class="brand-name"><span class="brand-mark"></span>SUMMIT RIDGE ESTATES</div>
    <div class="brand-slogan">"Building Value Together"</div>
  </div>
  <div class="pitch">
    <p>Are you considering selling your home? Want a simple, hassle-free transaction?</p>
    <p>No need to do any repairs, No realtor commissions,</p>
    <p>No closing costs....No headaches.</p>
    <p>We buy houses for cash and can close quickly!</p>
    <p class="pitch-close">Let us help you with your real estate needs...!</p>
  </div>
</section>

<section class="card card--front" aria-label="Card front">
  <div class="brand">
    <div class="brand-name"><span class="brand-mark"></span>SUMMIT RIDGE ESTATES</div>
    <div class="brand-slogan">"Building Value Together"</div>
  </div>

  <div class="holder">
    <div class="holder-name">Dale Harwick</div>
    <div class="holder-role">Managing Member</div>
  </div>

  <div class="divider"></div>

  <ul class="contacts">
    <li>
      <svg viewBox="0 0 16 16" aria-hidden="true"><circle cx="8" cy="8" r="8" fill="#1f63b8"/><path d="M5 4.5h1.6l.7 1.8-.9.7a5 5 0 0 0 2.6 2.6l.7-.9 1.8.7v1.6c-3.6.3-6.8-2.9-6.5-6.5z" fill="#fff"/></svg>
      (702) 555-0143
    </li>
    <li>
      <svg viewBox="0 0 16 16" aria-hidden="true"><circle cx="8" cy="8" r="8" fill="#1f63b8"/><rect x="5.5" y="4" width="5" height="3" fill="#fff"/><rect x="4" y="7" width="8" height="3.5" rx=".6" fill="#fff"/><rect x="5.5" y="10" width="5" height="2" fill="#fff"/></svg>
      (702) 555-0187
    </li>
    <li>
      <svg viewBox="0 0 16 16" aria-hidden="true"><circle cx="8" cy="8" r="8" fill="#1f63b8"/><rect x="4" y="5" width="8" height="6" rx=".6" fill="#fff"/><path d="M4.3 5.4 8 8.3l3.7-2.9" stroke="#1f63b8" stroke-width=".9" fill="none"/></svg>
      SummitRidgeEstate@hollowmail.test
    </li>
    <li class="web">
      <svg viewBox="0 0 16 16" aria-hidden="true"><circle cx="8" cy="8" r="8" fill="#1f63b8"/><path d="M8 3.6a2.9 2.9 0 0 0-2.9 2.9C5.1 8.8 8 12.4 8 12.4s2.9-3.6 2.9-5.9A2.9 2.9 0 0 0 8 3.6z" fill="#fff"/><circle cx="8" cy="6.5" r="1.1" fill="#1f63b8"/></svg>
      www.SummitRidgeEstates.test
    </li>
  </ul>

  <div class="office">
    <div class="office-name">Summit Ridge Pvt Ltd</div>
    <div>4821 Corliss Pkwy ste 207-300</div>
    <div>Cedar Hollow, NV 89321</div>
  </div>

  <div class="tagline-band">We buy houses for cash....no repairs, no commissions, no fees!</div>
</section>

</body>
</html>
```